Zolvana Stationary and Branding Documents

Corporate Identity Branding stationary needed for IT Recruiting Firm.

I already have a Logo, business cards and website. I need to get designs completed for the remaining corporate identity documents.

The documentation should use similar colors as my website and business card. The designs should modern and clean.

http://zolvanaworks.example/

Target Market(s)

Information Technology Industry

Industry/Entity Type

Information Technology

Colors
3377b5
0255a3
fbee3e
f78f20
f37122
33a6d7
000000
0592cd

Requirements
Must have
• Letter Head
• Folder Design
• PowerPoint Design
• Invoice
• Envelope
Nice to have
• Proposal
• Flyer
• Brochure
Should not have
• Logo
• Business Cards
• Website

```html
<!DOCTYPE html>
<html lang="en">
<head>
<meta charset="utf-8">
<title>Zolvana Letterhead</title>
<link href="https://fonts.googleapis.com/css2?family=Source+Sans+3:wght@400;600;700&display=swap" rel="stylesheet">
<style>
  :root {
    --backdrop: #e4e5e7;
    --paper: #ffffff;
    --brand-blue: #0a589e;
    --charcoal: #333333;
    --ink: #2b2b2b;
    --soft-ink: #444444;
    --rule: #777777;
    --white: #ffffff;
  }
  * { box-sizing: border-box; margin: 0; padding: 0; }
  html, body {
    width: 1200px; height: 1200px; overflow: hidden;
    background: var(--backdrop);
    font-family: "Source Sans 3", Arial, sans-serif;
  }
  .letterhead {
    position: absolute; left: 190px; top: 20px;
    width: 820px; height: 1160px;
    background: var(--paper);
    overflow: hidden;
  }
  .brand {
    position: absolute; top: 66px; left: 0; width: 100%;
    text-align: center;
  }
  .brand-name {
    font-size: 60px; font-weight: 600; color: var(--brand-blue);
    letter-spacing: 1px; line-height: 1;
  }
  .brand-tagline {
    margin-top: 6px;
    font-size: 17px; font-weight: 400; color: var(--brand-blue);
    letter-spacing: 1px;
  }
  .brand-address {
    margin-top: 6px; font-size: 14px; color: var(--ink);
  }
  .recipient {
    position: absolute; left: 122px; top: 223px;
    color: var(--ink);
  }
  .recipient .salutation { font-size: 14px; font-weight: 700; }
  .recipient .blank {
    display: inline-block; width: 78px; border-bottom: 1px solid var(--ink);
  }
  .recipient .designation { font-size: 9.5px; margin-top: 0; }
  .recipient .company { font-size: 9.5px; font-weight: 700; margin-top: 2px; }
  .letter-date {
    position: absolute; right: 120px; top: 223px;
    font-size: 14px; font-weight: 700; color: var(--ink);
  }
  .letter-body {
    position: absolute; left: 122px; top: 305px; width: 580px;
    font-size: 13.2px; line-height: 16.5px; color: var(--soft-ink);
    text-align: justify;
  }
  .letter-body p { margin-bottom: 20px; }
  .sign-off {
    position: absolute; left: 591px; top: 848px; color: var(--ink);
  }
  .sign-off .name { font-size: 16.5px; font-weight: 700; letter-spacing: 0.5px; line-height: 1.2; }
  .sign-off .role { font-size: 13px; margin-top: 1px; }
  .signature-area {
    position: absolute; left: 588px; top: 905px; width: 126px; height: 32px;
    background: linear-gradient(180deg, #ffffff 0%, #ececec 100%);
    border-bottom: 1px solid var(--rule);
  }
  .footer-shapes { position: absolute; left: 0; top: 0; }
  .contact-row {
    position: absolute; left: 0; top: 1103px; width: 100%;
    font-size: 10px; color: var(--white);
  }
  .contact-item {
    position: absolute; top: 0; height: 20px;
    display: flex; align-items: center; gap: 7px;
  }
  .contact-item svg { display: block; }
</style>
</head>
<body>
  <main class="letterhead">
    <header class="brand">
      <div class="brand-name">Zolvana</div>
      <div class="brand-tagline">BUSINESS SOLUTION LLC</div>
      <div class="brand-address">Two Harbor Plaza 410 Linden Avenue</div>
    </header>

    <section class="recipient">
      <div class="salutation">Dear, Mr<span class="blank">&nbsp;</span></div>
      <div class="designation">Designation</div>
      <div class="company">COMPANY NAME</div>
    </section>
    <div class="letter-date">DATE:1/5/2018</div>

    <section class="letter-body">
      <p>Lorem Ipsum is simply dummy text of the printing and typesetting industry. Lorem Ipsum has been the industry's standard dummy text ever since the1500s,when an unknown printer took a galley of type and scrambled it to make a type specimen book. It has survived not only five centuries, but also the leap into electronic typesetting, remaining essentially unchanged. It was popularised in the 1960s with the release of Quillmark sheets containing Lorem Ipsum passages, and more recently with desktop publishing software like Folio Layout including versions of Lorem Ipsum.</p>
      <p>Lorem Ipsum is simply dummy text of the printing and typesetting industry. Lorem Ipsum has been the industry's standard dummy text ever since the1500s,when an unknown printer took a galley of type and scrambled it to make a type specimen book. It has survived not only five centuries, but also the leap into electronic typesetting, remaining essentially unchanged. It was popularised in the 1960s with the release of Quillmark sheets containing Lorem Ipsum passages, and more recently with desktop publishing software like Folio Layout including versions of Lorem Ipsum.</p>
      <p>Lorem Ipsum is simply dummy text of the printing and typesetting industry. Lorem Ipsum has been the industry's standard dummy text ever since the1500s,when an unknown printer took a galley of type and scrambled it to make a type specimen book. It has survived not only five centuries, but also the leap into electronic typesetting, remaining essentially unchanged. It was popularised in the 1960s with the release of Quillmark sheets containing Lorem Ipsum passages, and more recently with desktop publishing software like Folio Layout including versions of Lorem Ipsum.</p>
      <p>Lorem Ipsum is simply dummy text of the printing and typesetting industry. Lorem Ipsum has been the industry's standard dummy text ever since the1500s,when an unknown printer took a galley of type and scrambled it to make a type specimen book. It has survived not only five centuries, but also the leap into electronic typesetting, remaining essentially unchanged. It was popularised in the 1960s with the release of Quillmark sheets containing Lorem Ipsum passages, and more recently with desktop publishing software like Folio Layout including versions of Lorem Ipsum.</p>
    </section>

    <section class="sign-off">
      <div class="name">YOUR NAME</div>
      <div class="role">Designation</div>
    </section>
    <div class="signature-area" role="img" aria-label="Handwritten signature"></div>

    <svg class="footer-shapes" width="820" height="1160" viewBox="0 0 820 1160" aria-hidden="true">
      <polygon points="0,988 443,1029 0,1096" fill="var(--charcoal)"/>
      <polygon points="0,1096 820,973 820,1160 0,1160" fill="var(--brand-blue)"/>
    </svg>

    <footer class="contact-row">
      <div class="contact-item" style="left:200px">
        <svg width="14" height="16" viewBox="0 0 14 16"><path d="M3 1 L5.5 1 L6.5 5 L4.8 6.3 C5.6 8.6 6.8 10.2 8.6 11.3 L10 9.6 L13.5 10.8 L13.5 13.5 C13.5 14.5 12.5 15.2 11.3 15 C5.8 14 1.5 9 1 3 C0.9 1.8 1.8 1 3 1 Z" fill="var(--white)"/></svg>
        <span>5550142876</span>
      </div>
      <div class="contact-item" style="left:331px">
        <svg width="18" height="12" viewBox="0 0 18 12"><rect x="0.75" y="0.75" width="16.5" height="10.5" fill="none" stroke="var(--white)" stroke-width="1.5"/><path d="M1 1 L9 7 L17 1 M1 11 L7 5.5 M17 11 L11 5.5" fill="none" stroke="var(--white)" stroke-width="1.3"/></svg>
        <span>info@zolvanaworks.example</span>
      </div>
      <div class="contact-item" style="left:505px">
        <svg width="20" height="20" viewBox="0 0 20 20"><g fill="none" stroke="var(--white)" stroke-width="1.3"><circle cx="10" cy="10" r="8.5"/><ellipse cx="10" cy="10" rx="3.8" ry="8.5"/><path d="M1.5 10 H18.5 M3 5.5 H17 M3 14.5 H17"/></g></svg>
        <span>www.zolvanaworks.example</span>
      </div>
    </footer>
  </main>
</body>
</html>
```